TK Stationery - Modern Contemporary

Develop modern template for Letterhead and Stationery (business card, letterhead, envelopes) using the TK Logo and Icon

Colors
0054AA
0677BA
7BADD7
CADEEF
E8F1F8
00AB8E
00BBA5
67D7C9
C6EFE9
E9F9F6
EE7325
F08F49
F5BC92
FAE3D3
FDF4ED
6B429C
8869AF
B7A5CE
E3DAEB
F3F0F8

```html
<!DOCTYPE html>
<html lang="en">
<head>
<meta charset="utf-8">
<title>Halvern – Business Card</title>
<link rel="stylesheet" href="https://fonts.googleapis.com/css2?family=Fraunces:opsz,wght@9..144,500;9..144,700&family=Tinos&display=swap">
<style>
  :root {
    --stage: #1c1c1e;
    --card: #111b26;
    --card-back: #0f1824;
    --pattern-a: #1a2340;
    --pattern-b: #27305c;
    --green: #1fb07a;
    --orange: #ee7325;
    --white: #f4f4f2;
    --rule: #9aa0a8;
  }
  * { margin: 0; padding: 0; box-sizing: border-box; }
  html, body { width: 1200px; height: 1108px; overflow: hidden; }
  body {
    background: var(--stage);
    position: relative;
    font-family: "Tinos", "Times New Roman", serif;
  }
  .card {
    position: absolute;
    top: 204px;
    width: 420px;
    height: 700px;
    border-radius: 24px;
    overflow: hidden;
  }
  .card--front { left: 150px; background: var(--card); }
  .card--back { left: 630px; background: var(--card-back); }

  .brand {
    font-family: "Fraunces", Georgia, serif;
    font-weight: 500;
    color: var(--white);
    letter-spacing: 6px;
    text-transform: uppercase;
    white-space: nowrap;
    text-align: center;
  }
  .card--front .brand {
    position: absolute; top: 150px; left: 0; right: 0;
    font-size: 54px;
  }

  .person {
    position: absolute; top: 370px; left: 0; right: 0;
    text-align: center;
  }
  .person-name {
    font-family: "Fraunces", Georgia, serif;
    font-weight: 700;
    color: var(--green);
    font-size: 36px;
    line-height: 1;
  }
  .person-title {
    color: var(--orange);
    font-size: 22px;
    margin-top: 4px;
  }

  .icon-row {
    position: absolute; top: 456px; left: 40px; right: 40px;
    display: flex; align-items: center; gap: 10px;
  }
  .icon-row .rule { flex: 1; height: 1px; background: var(--rule); }
  .icon {
    width: 40px; height: 40px; border-radius: 6px;
    background: var(--green);
    display: flex; align-items: center; justify-content: center;
  }

  .contact {
    position: absolute; top: 510px; left: 0; right: 0;
    text-align: center;
    color: var(--white);
    font-size: 22px;
    line-height: 30px;
  }
  .address-rule {
    position: absolute; top: 610px; left: 70px; right: 70px;
    height: 1px; background: var(--rule);
  }
  .address {
    position: absolute; top: 620px; left: 0; right: 0;
    text-align: center;
    color: var(--white);
    font-size: 20px;
    line-height: 26px;
  }

  .back-pattern {
    position: absolute; inset: 0;
    background: linear-gradient(150deg, var(--pattern-b) 0%, var(--pattern-a) 45%, var(--card-back) 100%);
  }
  .card--back .brand {
    position: absolute; top: 400px; left: 0; right: 0;
    font-size: 48px;
  }
</style>
</head>
<body>
  <section class="card card--front">
    <div class="brand">Halvern</div>

    <div class="person">
      <div class="person-name">Daniel Reyes</div>
      <div class="person-title">Managing Director</div>
    </div>

    <div class="icon-row">
      <span class="rule"></span>
      <span class="icon" aria-label="Phone">
        <svg width="24" height="24" viewBox="0 0 24 24"><path fill="#fff" d="M6.6 10.8a15 15 0 0 0 6.6 6.6l2.2-2.2c.3-.3.7-.4 1-.2 1.1.4 2.3.6 3.6.6.6 0 1 .4 1 1V20c0 .6-.4 1-1 1A17 17 0 0 1 3 4c0-.6.4-1 1-1h3.5c.6 0 1 .4 1 1 0 1.3.2 2.5.6 3.6.1.3 0 .7-.2 1z"/></svg>
      </span>
      <span class="icon" aria-label="Email">
        <svg width="24" height="24" viewBox="0 0 24 24"><rect x="3" y="5.5" width="18" height="13" rx="1" fill="none" stroke="#fff" stroke-width="2"/><path d="M3.5 6.5 12 13l8.5-6.5" fill="none" stroke="#fff" stroke-width="2"/></svg>
      </span>
      <span class="icon" aria-label="Website">
        <svg width="24" height="24" viewBox="0 0 24 24"><circle cx="12" cy="12" r="9" fill="none" stroke="#fff" stroke-width="2"/><path d="M3 12h18M12 3c3 3 3 15 0 18M12 3c-3 3-3 15 0 18" fill="none" stroke="#fff" stroke-width="1.5"/></svg>
      </span>
      <span class="rule"></span>
    </div>

    <div class="contact">
      <p>044-210 583 617</p>
      <p>hello@halvern.com</p>
      <p>www.halvern.com</p>
    </div>
    <div class="address-rule"></div>
    <div class="address">
      <p>18 Harbour Lane, Suite 4</p>
      <p>30117, Portland</p>
    </div>
  </section>

  <section class="card card--back">
    <div class="back-pattern" role="img" aria-label="Faint repeating company-name pattern in deep blue across the card"></div>
    <div class="brand">Halvern</div>
  </section>
</body>
</html>
```